Marvane Pour Over Coffee Filter Packaging Design

We are a brand new company starting to sell coffee related products. The coffee filter that we are about to sell will be copper color. We are working on the exact product picture, but a temporary one will be in uploaded files.We want the box to be simple, yet elegant and not too flashy. We prefer black, rose gold, white design, but are open to other designs. The uploaded files are just samples of what we like. "Marvane" means "owl" in French, we want an owl to be on the logo. Coffee related logo design is best, but we are open to other ideas. Size of this particular packaging is 14x14x12 cm

Target Market(s)

Online Retail

Industry/Entity Type

It Company

Logo Text

"Marvane Products" and "Marvane"

Other font styles liked:
• Your choice

Colors

Designer to choose colors to be used in the design.

Requirements
Must have
• Owl on the logo. Product description in a word file attached.
Nice to have
• Read product description

```html
<!DOCTYPE html>
<html lang="en">
<head>
<meta charset="UTF-8">
<title>Marvane Pour Over Coffee Filter – Box Front</title>
<link href="https://fonts.googleapis.com/css2?family=Heebo:wght@200;300&family=Roboto+Condensed:wght@300;400&family=Pinyon+Script&display=swap" rel="stylesheet">
<style>
  :root {
    --page-bg: #f4f2f1;
    --panel-bg: #ffffff;
    --rose-gold: #e2b3a3;
    --rose-gold-deep: #cf9884;
    --rose-text: #d9876f;
    --ink: #1b1b1b;
    --copper-light: #f1d2bd;
    --copper-mid: #c98a62;
    --copper-dark: #8a4f2c;
    --script-ink: #9a5b3c;
  }
  * { box-sizing: border-box; margin: 0; padding: 0; }
  html, body {
    width: 1200px;
    height: 1200px;
    overflow: hidden;
    background: var(--page-bg);
  }
  .canvas {
    position: relative;
    width: 1200px;
    height: 1200px;
  }
  .box-front {
    position: absolute;
    left: 150px;
    top: 150px;
    width: 900px;
    height: 900px;
    background: var(--panel-bg);
    box-shadow: 0 6px 30px rgba(0,0,0,0.08);
    overflow: hidden;
  }
  .lid-band {
    position: absolute;
    left: 0;
    top: 0;
    width: 100%;
    height: 100px;
    background: linear-gradient(180deg, var(--rose-gold) 0%, var(--rose-gold-deep) 100%);
  }
  .brand-name {
    position: absolute;
    left: 90px;
    top: 250px;
    font-family: "Heebo", sans-serif;
    font-weight: 200;
    font-size: 112px;
    letter-spacing: 2px;
    line-height: 1;
    color: var(--ink);
  }
  .product-line {
    position: absolute;
    left: 96px;
    top: 392px;
    font-family: "Roboto Condensed", sans-serif;
    font-weight: 400;
    font-size: 30px;
    color: var(--rose-text);
  }
  .product-photo {
    position: absolute;
    left: 500px;
    top: 430px;
    width: 350px;
    height: 400px;
    border-radius: 48% 48% 40% 40% / 30% 30% 60% 60%;
    background: radial-gradient(ellipse at 45% 35%, var(--copper-light) 0%, var(--copper-mid) 55%, var(--copper-dark) 100%);
    opacity: 0.9;
  }
  .tagline {
    position: absolute;
    left: 90px;
    top: 680px;
    width: 390px;
    font-family: "Pinyon Script", cursive;
    font-size: 21px;
    line-height: 1.9;
    color: var(--script-ink);
    white-space: nowrap;
  }
</style>
</head>
<body>
  <div class="canvas">
    <section class="box-front">
      <div class="lid-band"></div>
      <h1 class="brand-name">MARVANE</h1>
      <p class="product-line">Pour Over Coffee Filter</p>
      <div class="product-photo" role="img" aria-label="Photo of the copper heart-shaped pour over coffee filter with mesh cone and heart base"></div>
      <p class="tagline">
        A good cup of coffee shared with a friend<br>
        is like capturing happiness in a cup!<br>
        Share the liquid gold (coffee that is) with others!
      </p>
    </section>
  </div>
</body>
</html>
```